Business card design needed

I would like a one sided black business card with the information provided above. Refer to my website www.brightvolleyracquets.com.au for an example of colors I have used for my site, would like to keep this consistent for my business cards also, I will upload my logo below.

I am a new small business that provides tennis customers with racquet re stringing, tennis strings and accessories.

Industry/Entity Type

Small Business

Contact Information for Business Card

Bright Volley Tennis

Owen Whitby
Managing Director

brightvolleyracquets@mailbox.example
www.brightvolleyracquets.com.au
0491 726 305

Racquet Restringing/Tennis Strings/Accessories

Requirements
Must have
• Must have my logo and card must be black

```html
<!DOCTYPE html>
<html lang="en">
<head>
<meta charset="utf-8">
<title>Bright Volley Tennis – Business Card</title>
<link rel="stylesheet" href="https://fonts.googleapis.com/css2?family=Roboto:wght@400;700&display=swap">
<style>
  :root {
    --stage: #ecebe8;
    --card-black: #000000;
    --brand-blue: #1f4479;
    --brand-lime: #bfdc2a;
    --text-white: #ffffff;
  }
  * { margin: 0; padding: 0; box-sizing: border-box; }
  html, body {
    width: 1200px;
    height: 475px;
    overflow: hidden;
    background: var(--stage);
    font-family: "Roboto", Arial, sans-serif;
  }
  .stage { position: relative; width: 1200px; height: 475px; }

  .card {
    position: absolute;
    width: 548px;
    height: 314px;
    background: var(--card-black);
    overflow: hidden;
  }
  .card--front { left: 23px; top: 80px; border-radius: 22px 0 22px 0; }
  .card--back  { left: 607px; top: 86px; border-radius: 0 22px 0 22px; }

  .front-swoosh { position: absolute; inset: 0; width: 548px; height: 314px; }

  .holder {
    position: absolute;
    right: 30px;
    top: 34px;
    text-align: right;
    color: var(--brand-lime);
  }
  .holder__name { font-size: 19px; font-weight: 400; letter-spacing: 0.5px; text-transform: uppercase; line-height: 1.1; }
  .holder__role { font-size: 14px; font-weight: 400; margin-top: 4px; }

  .brand-mark {
    position: absolute;
    display: flex;
    align-items: center;
    gap: 10px;
    color: var(--brand-lime);
    font-weight: 700;
    font-size: 27px;
    letter-spacing: 0.3px;
    white-space: nowrap;
  }
  .brand-mark__dot {
    width: 34px; height: 34px;
    border-radius: 50%;
    background: var(--brand-lime);
    flex: none;
  }
  .card--front .brand-mark { left: 22px; top: 133px; }
  .card--back .brand-mark { left: 50%; top: 112px; transform: translateX(-50%); }

  .contact {
    position: absolute;
    right: 28px;
    bottom: 28px;
    text-align: right;
    color: var(--text-white);
    font-size: 14px;
    line-height: 21px;
    letter-spacing: 0.3px;
  }

  .back-url {
    position: absolute;
    left: 0; right: 0;
    top: 240px;
    text-align: center;
    color: var(--text-white);
    font-size: 14px;
    letter-spacing: 1.4px;
  }
</style>
</head>
<body>
<main class="stage">

  <section class="card card--front" aria-label="Business card front">
    <svg class="front-swoosh" viewBox="0 0 548 314" aria-hidden="true">
      <path d="M0,0 H548 V150 Q250,-20 0,30 Z" fill="var(--brand-blue)"/>
      <path d="M0,34 Q250,-12 548,156 L548,172 Q245,6 0,46 Z" fill="var(--brand-lime)"/>
    </svg>

    <div class="holder">
      <p class="holder__name">Owen Whitby</p>
      <p class="holder__role">Managing Director</p>
    </div>

    <div class="brand-mark">
      <span class="brand-mark__dot"></span>
      <span class="brand-mark__name">Bright Volley Tennis</span>
    </div>

    <address class="contact" style="font-style: normal;">
      <p>P : 0491 726 305</p>
      <p>E : brightvolleyracquets@mailbox.example</p>
      <p>W: www.brightvolleyracquets.com.au</p>
    </address>
  </section>

  <section class="card card--back" aria-label="Business card back">
    <div class="brand-mark">
      <span class="brand-mark__dot"></span>
      <span class="brand-mark__name">Bright Volley Tennis</span>
    </div>
    <p class="back-url">www.brightvolleyracquets.com.au</p>
  </section>

</main>
</body>
</html>
```